Roofing Contractor business card redesign

I want to redesign my business card with a fresh, eye catching concept

Target Market(s)

Residential Roofing Clients, potential employees, and subcontractors.

Industry/Entity Type

Business

Colors

Designer to choose colors to be used in the design.

Requirements
Nice to have
• I just want something that's more pleasing to the eye. You can use a combination of either / or of my logos.

```html
<!DOCTYPE html>
<html lang="en">
<head>
<meta charset="utf-8">
<title>Sturdy Crew – Business Card</title>
<link rel="stylesheet" href="https://fonts.googleapis.com/css2?family=Roboto:wght@400;700&family=Roboto+Condensed:wght@300;700&family=Lato:wght@400&display=swap">
<style>
  :root {
    --backdrop: #5c5c5c;
    --paper: #ffffff;
    --brown: #3e1d1c;
    --orange: #e8771e;
    --ink: #1c1c1c;
    --yellow-light: #fbd64a;
    --yellow: #f7c21c;
    --yellow-deep: #f0b310;
  }
  * { box-sizing: border-box; margin: 0; padding: 0; }
  html, body { width: 1200px; height: 1200px; overflow: hidden; }
  body { background: var(--backdrop); position: relative; font-family: "Roboto", sans-serif; }

  .card {
    position: absolute; top: 449px; width: 540px; height: 302px;
    border-radius: 8px; overflow: hidden;
  }
  .card--front { left: 50px; background: var(--paper); }
  .card--back {
    left: 610px;
    background: radial-gradient(ellipse at 50% 25%, var(--yellow-light) 0%, var(--yellow) 55%, var(--yellow-deep) 100%);
    display: flex; flex-direction: column; align-items: center; justify-content: center;
  }

  .logo-circle {
    position: absolute; left: 53px; top: 23px; width: 146px; height: 146px;
    border-radius: 50%;
    background: radial-gradient(circle at 50% 45%, #f2a55a 0%, #d4652a 45%, var(--brown) 75%);
    border: 7px solid var(--brown);
  }

  .identity { position: absolute; left: 246px; top: 30px; }
  .identity__name { font-family: "Roboto", sans-serif; font-weight: 700; font-size: 24px; color: var(--brown); line-height: 1; }
  .identity__title { font-size: 14px; color: var(--orange); line-height: 18px; margin-top: 8px; }
  .identity__address { font-size: 15.5px; color: var(--ink); line-height: 21px; margin-top: 32px; }

  .contact-band {
    position: absolute; left: 0; bottom: 0; width: 100%; height: 115px;
    background: var(--brown); color: var(--paper);
  }
  .contact-band__phone-icon { position: absolute; left: 24px; top: 20px; width: 36px; height: 50px; }
  .contact-band__phones, .contact-band__links {
    position: absolute; top: 16px;
    font-family: "Roboto Condensed", sans-serif; font-weight: 300; font-size: 25px; line-height: 29px;
  }
  .contact-band__phones { left: 68px; }
  .contact-band__links { left: 246px; }
  .contact-band__links div { display: flex; align-items: center; gap: 6px; }
  .contact-band__links svg { width: 22px; height: 22px; flex: none; }
  .contact-band__footer {
    position: absolute; left: 22px; right: 22px; bottom: 12px;
    display: flex; align-items: center; gap: 12px;
    font-family: "Lato", sans-serif; font-size: 12.5px; white-space: nowrap;
  }
  .contact-band__footer::before, .contact-band__footer::after {
    content: ""; flex: 1; height: 2px; background: var(--paper);
  }

  .brand { display: flex; align-items: center; gap: 14px; }
  .brand__name, .brand__tagline {
    font-family: "Roboto Condensed", sans-serif; font-weight: 700; color: var(--brown);
  }
  .brand__name { font-size: 62px; line-height: 1; letter-spacing: -1px; }
  .brand__mark { width: 22px; height: 22px; border-radius: 50%; background: var(--brown); }
  .brand__tagline { font-size: 21px; margin-top: 6px; }
</style>
</head>
<body>
  <section class="card card--front" aria-label="Business card front">
    <div class="logo-circle" role="img" aria-label="Company logo emblem"></div>

    <div class="identity">
      <h1 class="identity__name">Dale Mercer</h1>
      <p class="identity__title">Ridgeline Certified Roof Inspector<br>Licensed Property Adjuster</p>
      <p class="identity__address">4580 Cedar Hollow Drive Suite, 118<br>Fairview, TX 75069</p>
    </div>

    <div class="contact-band">
      <svg class="contact-band__phone-icon" viewBox="0 0 36 50" fill="none" stroke="#fff" stroke-width="2.4" stroke-linejoin="round" aria-hidden="true">
        <path d="M9 3 L15 3 L17 13 L12 16 C12 24 16 32 22 36 L27 32 L34 39 L30 46 C18 46 4 30 4 10 Z"/>
      </svg>
      <div class="contact-band__phones">
        <div>(555) 218-4470</div>
        <div>(555) 639-2100</div>
      </div>
      <div class="contact-band__links">
        <div>
          <svg viewBox="0 0 22 22" aria-hidden="true"><circle cx="11" cy="11" r="10.5" fill="#fff"/><rect x="5" y="7" width="12" height="8" fill="none" stroke="#3e1d1c" stroke-width="1.4"/><path d="M5 7 L11 12 L17 7" fill="none" stroke="#3e1d1c" stroke-width="1.4"/></svg>
          <span>dale@sturdycrewtx.com</span>
        </div>
        <div>
          <svg viewBox="0 0 22 22" aria-hidden="true"><circle cx="11" cy="11" r="10.5" fill="#fff"/><g fill="none" stroke="#3e1d1c" stroke-width="1.2"><circle cx="11" cy="11" r="6"/><ellipse cx="11" cy="11" rx="2.6" ry="6"/><path d="M5 11 H17 M6 8 H16 M6 14 H16"/></g></svg>
          <span>www.sturdycrewgc.com</span>
        </div>
      </div>
      <div class="contact-band__footer">Sturdy Crew General Contractors, Inc.</div>
    </div>
  </section>

  <section class="card card--back" aria-label="Business card back">
    <div class="brand">
      <span class="brand__name">Sturdy Crew</span>
      <span class="brand__mark" aria-hidden="true"></span>
    </div>
    <p class="brand__tagline">General Contractors, Inc.</p>
  </section>
</body>
</html>
```